Velk Partners Building Business Cards

We need a business card that reflects our business as "Solar Experts" in San Diego. Browse our website www.velkpartners.example our License needs to be displayed as "CSLB# 3867140" our phone number is (619) 555-0187

Save thousands on your electric bills and increase the value of your home while helping to protect the environment. Our solar installation experts will help you design the system that's right for you, using only the highest quality equipment that will look great and give you ideal performance. Our goal is to make you energy independent, and get your electric bill to 0.

Paul Osterby
(619) 555-0187
paul@velkpartners.example

Target Market(s)

Home owners in san diego looking for solar

Industry/Entity Type

Solar Energy

Contact Information for Business Card

Paul Osterby
(619) 555-0187
paul@velkpartners.example

Font styles to use
Other font styles liked:
• Use our logo font

Requirements
Must have
• License needs to be displayed as "CSLB# 3867140" our phone number is (619) 555-0187
Nice to have
• Real images of rooftop home solar in san diego
Should not have
• our business address

```html
<!DOCTYPE html>
<html lang="en">
<head>
<meta charset="utf-8">
<title>Velk Partners Building – Business Card</title>
<link rel="stylesheet" href="https://fonts.googleapis.com/css2?family=Montserrat:wght@800&family=Open+Sans:wght@400;600&display=swap">
<style>
  :root {
    --navy: #1a3a73;
    --gold: #f5ab0c;
    --white: #ffffff;
    --paper: #e9ecec;
    --rule-grey: #8c9ab5;
    --band-on-navy: linear-gradient(to bottom, rgba(245,171,12,0.28), rgba(245,171,12,0.10));
    --band-on-white: linear-gradient(to bottom, rgba(26,58,115,0.22), rgba(26,58,115,0.07));
  }
  * { box-sizing: border-box; margin: 0; padding: 0; }
  html, body { width: 1200px; height: 812px; overflow: hidden; }
  body {
    background: var(--paper);
    font-family: "Open Sans", Arial, sans-serif;
    position: relative;
  }
  .card {
    position: absolute;
    top: 251px;
    width: 540px;
    height: 310px;
    overflow: hidden;
    box-shadow: 0 6px 18px rgba(0,0,0,0.12);
  }
  .card--back { left: 40px; background: var(--navy); }
  .card--front { left: 620px; background: var(--white); }

  .edge-band {
    position: absolute;
    left: 0;
    width: 100%;
    height: 22px;
  }
  .edge-band--top { top: 0; }
  .edge-band--bottom { bottom: 0; transform: scaleY(-1); }
  .card--back .edge-band { background: var(--band-on-navy); }
  .card--front .edge-band { background: var(--band-on-white); }

  .brand-name {
    font-family: "Montserrat", Arial, sans-serif;
    font-weight: 800;
    letter-spacing: -0.5px;
    line-height: 1.05;
  }
  .card--back .brand-name {
    position: absolute;
    left: 36px;
    top: 112px;
    width: 190px;
    font-size: 27px;
    color: var(--gold);
  }
  .divider {
    position: absolute;
    left: 250px;
    top: 88px;
    width: 1px;
    height: 134px;
    background: var(--rule-grey);
  }
  .contact {
    position: absolute;
    left: 274px;
    top: 86px;
    color: var(--white);
    font-size: 13px;
    line-height: 1.45;
  }
  .contact__name {
    font-family: "Montserrat", Arial, sans-serif;
    font-weight: 800;
    font-size: 19px;
    color: var(--gold);
    line-height: 1.2;
  }
  .contact__license { margin-bottom: 4px; }
  .contact__row { display: flex; align-items: center; gap: 7px; }
  .contact__row svg { width: 12px; height: 12px; flex: none; }

  .card--front .brand-name {
    position: absolute;
    left: 0;
    right: 0;
    top: 128px;
    text-align: center;
    font-size: 38px;
    color: var(--navy);
  }
</style>
</head>
<body>

<section class="card card--back" aria-label="Business card, contact side">
  <div class="edge-band edge-band--top" role="img" aria-label="Measuring-ruler border along the top edge"></div>

  <div class="brand-name">Velk Partners Building</div>
  <div class="divider"></div>

  <div class="contact">
    <div class="contact__name">Paul Osterby</div>
    <div>CEO/Founder</div>
    <div class="contact__license">CSLB# 3867140</div>
    <div class="contact__row">
      <svg viewBox="0 0 12 12" aria-hidden="true"><path fill="#f5ab0c" d="M2.3 1 4.2 3 3.4 4.4c.7 1.6 2.2 3.1 3.8 3.8L8.6 7.4 10.6 9.3 9.6 11C5.3 10.8 1.2 6.7 1 2.4Z"/></svg>
      <span>(619) 555-0187</span>
    </div>
    <div class="contact__row">
      <svg viewBox="0 0 12 12" aria-hidden="true"><rect x="0.5" y="2.5" width="11" height="7.5" fill="#f5ab0c"/><path d="M0.8 3 6 7 11.2 3" fill="none" stroke="#1a3a73" stroke-width="1"/></svg>
      <span>paul@velkpartners.example</span>
    </div>
    <div class="contact__row">
      <svg viewBox="0 0 12 12" aria-hidden="true"><circle cx="6" cy="6" r="5.5" fill="#f5ab0c"/><path d="M6 .5v11M.5 6h11M6 .5c-2.8 3-2.8 8 0 11M6 .5c2.8 3 2.8 8 0 11" fill="none" stroke="#1a3a73" stroke-width=".8"/></svg>
      <span>www.velkpartners.example</span>
    </div>
  </div>

  <div class="edge-band edge-band--bottom" role="img" aria-label="Measuring-ruler border along the bottom edge"></div>
</section>

<section class="card card--front" aria-label="Business card, name side">
  <div class="edge-band edge-band--top" role="img" aria-label="Measuring-ruler border along the top edge"></div>

  <div class="brand-name">Velk Partners Building</div>

  <div class="edge-band edge-band--bottom" role="img" aria-label="Measuring-ruler border along the bottom edge"></div>
</section>

</body>
</html>
```